New clean and fresh corporate PPT template for Telecom equipment maker

MPK (VORQEX MPKT) is a telecom equipment maker in Silicon Valley. Our current PPT template that goes with http://peltrovane.com is overbuilt, dark, huge in file size, and looks the opposite of fresh and clean.
Our new microsite @ http://investor-mpkt.com is the direction we want to go. We are B2B, selling to telecom operators, but still want something that looks clean and fresh and not stuffy, hence primarily white background with maximum whitespace in 16:9 format.
Style guidelines attached, exclusive use of approved colors required, the master should remain as simple as possible, and we want the file size to stay reasonable (i.e. less is better). Features we would like include:
- Lato font built-in to the template
- Text boxes with standard size fonts, that automatically get smaller with indention
- An interesting bullet style, nothing crazy, but with visual interest
- A pre-selected table format that is clean and allows for high-density tables with many rows & columns
- Whichever standard slides layouts in the master you think would help result in slides that are found in the current deck, without someone needing to build their own slide

```html
<!DOCTYPE html>
<html lang="en">
<head>
<meta charset="utf-8">
<title>Global FTTH Demand</title>
<link href="https://fonts.googleapis.com/css2?family=Lato:ital,wght@0,400;0,700;0,900;1,400&family=Arimo:ital,wght@0,700;1,400;1,700&display=swap" rel="stylesheet">
<style>
  :root {
    --slate: #4b5a6d;
    --navy: #1f4e96;
    --body: #4d5763;
    --muted: #5f6670;
    --teal: #4cc4c4;
    --green: #8dc63f;
    --coral: #f0605d;
    --bar: #29a8e0;
    --arrow: #92d050;
    --panel: #f2f2f2;
    --ink: #111111;
    --mark: #a9adb2;
  }
  * { margin: 0; padding: 0; box-sizing: border-box; }
  html, body { width: 1200px; height: 675px; overflow: hidden; background: #fff; }
  .slide { position: relative; width: 1200px; height: 675px; font-family: "Lato", sans-serif; color: var(--body); }

  .slide-title {
    position: absolute; top: 38px; left: 0; width: 1200px; text-align: center;
    font-size: 40px; font-weight: 700; color: var(--slate); letter-spacing: -0.2px;
  }
  .title-rule { position: absolute; top: 101px; left: 537px; display: flex; height: 4px; }
  .title-rule span { width: 42px; height: 4px; }
  .title-rule .teal { background: var(--teal); }
  .title-rule .green { background: var(--green); }
  .title-rule .coral { background: var(--coral); }

  .lead, .closing {
    position: absolute; left: 41px; width: 520px;
    font-size: 20px; font-weight: 700; color: var(--navy); line-height: 24px;
  }
  .lead { top: 121px; }
  .closing { top: 454px; }

  .factors { position: absolute; top: 230px; left: 58px; list-style: none; }
  .factors > li { position: relative; padding-left: 18px; font-size: 20px; font-weight: 700; color: var(--body); line-height: 28px; }
  .factors > li::before {
    content: ""; position: absolute; left: 1px; top: 11px; width: 7px; height: 7px; border-radius: 50%; background: var(--body);
  }
  .drivers { list-style: none; margin-top: 4px; margin-left: 5px; }
  .drivers li { position: relative; padding-left: 20px; font-size: 19px; font-weight: 400; line-height: 31.5px; }
  .drivers li::before { content: "-"; position: absolute; left: 0; top: 0; }

  .source { position: absolute; top: 565px; left: 38px; font-size: 14px; line-height: 18px; color: var(--muted); }

  .chart-panel {
    position: absolute; left: 611px; top: 128px; width: 514px; height: 475px;
    background: var(--panel); box-shadow: 0 1px 3px rgba(0,0,0,0.25);
  }
  .chart-title {
    position: absolute; top: 16px; left: 0; width: 100%; text-align: center;
    font-family: "Arimo", sans-serif; font-weight: 700; font-size: 22px; line-height: 29px; color: var(--ink); letter-spacing: 0.3px;
  }
  .chart-unit {
    position: absolute; top: 82px; left: 0; width: 100%; text-align: center;
    font-family: "Arimo", sans-serif; font-style: italic; font-size: 11px; color: var(--ink);
  }
  .chart-svg { position: absolute; left: 0; top: 0; }
  .chart-svg text { font-family: "Arimo", sans-serif; font-weight: 700; fill: var(--ink); }

  .brand { position: absolute; left: 16px; top: 619px; display: flex; align-items: center; gap: 8px; }
  .brand-square { width: 10px; height: 10px; background: var(--mark); }
  .brand-name { font-size: 30px; font-weight: 900; color: var(--mark); letter-spacing: 1px; }

  .copyright { position: absolute; top: 642px; left: 0; width: 1162px; text-align: center; font-size: 14px; color: var(--muted); }
  .page-rule { position: absolute; left: 1125px; top: 625px; width: 75px; height: 4px; background: var(--teal); }
  .page-number { position: absolute; left: 1127px; top: 634px; font-size: 18px; color: var(--slate); }
</style>
</head>
<body>
<main class="slide">
  <h1 class="slide-title">What’s Driving the Global Demand for Fiber to the Home?</h1>
  <div class="title-rule"><span class="teal"></span><span class="green"></span><span class="coral"></span></div>

  <p class="lead">The global fiber to the home (FTTH) market is expected to grow from $9.5 billion in 2017 to $36.5 billion in 2027—a 14%+ CAGR</p>

  <ul class="factors">
    <li>Factors contributing to this strong growth include:
      <ul class="drivers">
        <li>Growing video and data usage needs</li>
        <li>Government initiatives in various regions</li>
        <li>Internet of Things (IoT)</li>
        <li>Rising construction in emerging economies</li>
        <li>Increasing telecom sector investments</li>
      </ul>
    </li>
  </ul>

  <p class="closing">These strong growth drivers, along with our global presence and industry-leading solutions, position us to grow solidly over the next several years</p>

  <p class="source">Source: Northgate Market Research (NMR): “Fibre to the Home Market: Global<br>Industry Analysis (2012-2016) and Opportunity Assessment (2017-2017)</p>

  <section class="chart-panel" aria-label="Bar chart of global fiber to the home market size, 2017 to 2027">
    <h2 class="chart-title">Total Size of the Global Fiber to the<br>Home Market</h2>
    <p class="chart-unit">($ in billions)</p>
    <svg class="chart-svg" width="514" height="475" viewBox="611 128 514 475">
      <line x1="632" y1="563" x2="1104" y2="563" stroke="#d9d9d9" stroke-width="1"/>
      <g fill="var(--bar)">
        <rect x="639" y="479" width="27" height="84"/>
        <rect x="682" y="466" width="27" height="97"/>
        <rect x="726" y="452" width="27" height="111"/>
        <rect x="769" y="436" width="27" height="127"/>
        <rect x="812" y="417" width="27" height="146"/>
        <rect x="855" y="396" width="27" height="167"/>
        <rect x="899" y="373" width="27" height="190"/>
        <rect x="942" y="345" width="27" height="218"/>
        <rect x="986" y="313" width="27" height="250"/>
        <rect x="1028" y="277" width="27" height="286"/>
        <rect x="1071" y="236" width="27" height="327"/>
      </g>
      <g class="growth-arrow">
        <line x1="653" y1="551" x2="1060" y2="330" stroke="var(--arrow)" stroke-width="19"/>
        <polygon points="1084,316 1067.5,344.3 1051.3,314.5" fill="var(--arrow)"/>
        <polygon points="1084,316 1069,348 1048,310" fill="var(--arrow)"/>
        <text x="864" y="441" transform="rotate(-28.5 864 437)" text-anchor="middle" font-size="14" style="fill:#fff">14%+ CAGR</text>
      </g>
      <text x="652" y="473" text-anchor="middle" font-size="15">$9.5</text>
      <text x="1085" y="230" text-anchor="middle" font-size="15">$36.5</text>
      <text x="652" y="584" text-anchor="middle" font-size="15">2017</text>
      <text x="1085" y="584" text-anchor="middle" font-size="15">2027</text>
    </svg>
  </section>

  <div class="brand"><span class="brand-square"></span><span class="brand-name">MPK</span></div>
  <p class="copyright">© 2018 Marrowpeak Solutions – Proprietary and Confidential</p>
  <div class="page-rule"></div>
  <p class="page-number">8</p>
</main>
</body>
</html>
```